We are a recruitment company based in Norwich/Cambridge England.
I have included our company logo which we want to remain the same.

What we are looking for is a new creative Business card which will really stand out!!

Contact Information for Business Card

Harriet Dunmore
email: Harriet@plavex.co.uk
Address: Brackwell House
Fenmoor Enterprise Park
Partridge Way
Norwich
QB9 3KX
Tel:01632 960418

```html
<!DOCTYPE html>
<html lang="en">
<head>
<meta charset="utf-8">
<title>Plavex Business Card</title>
<link rel="stylesheet" href="https://fonts.googleapis.com/css2?family=Arimo:wght@400;700&display=swap">
<style>
  :root {
    --stage: #1c1d1f;
    --card: #26292b;
    --green: #7cc242;
    --grey: #9a9a9d;
    --rule: #4f6b2e;
    --font: "Arimo", Arial, sans-serif;
  }
  * { margin: 0; padding: 0; box-sizing: border-box; }
  html, body { width: 1200px; height: 800px; overflow: hidden; background: var(--stage); }
  .canvas { position: relative; width: 1200px; height: 800px; font-family: var(--font); }
  .card {
    position: absolute; width: 525px; height: 300px; background: var(--card);
    box-shadow: 0 18px 40px rgba(0,0,0,.55);
  }
  .card--front { left: 70px; top: 80px; display: flex; align-items: center; justify-content: center; }
  .card--back { left: 605px; top: 420px; }

  .brand { display: flex; align-items: center; gap: 14px; }
  .brand__dot { width: 46px; height: 46px; border-radius: 50%; background: var(--green); }
  .brand__name { font-weight: 700; font-size: 52px; color: var(--green); letter-spacing: -1px; }
  .card--back .brand { position: absolute; left: 40px; top: 108px; gap: 10px; }
  .card--back .brand__dot { width: 30px; height: 30px; }
  .card--back .brand__name { font-size: 34px; }

  .divider { position: absolute; left: 262px; top: 60px; width: 1px; height: 130px; background: var(--rule); }

  .contact { position: absolute; left: 285px; top: 62px; }
  .contact__name { font-weight: 700; font-size: 20px; color: var(--green); }
  .contact__role { font-size: 13px; color: var(--grey); margin-top: 2px; }
  .contact__list { list-style: none; margin-top: 16px; }
  .contact__item { display: flex; align-items: center; gap: 8px; font-size: 12.5px; color: var(--grey); margin-bottom: 8px; }
  .contact__icon { width: 16px; height: 16px; flex: none; }

  .address { position: absolute; left: 40px; right: 40px; bottom: 32px; font-size: 12.5px; color: var(--grey); letter-spacing: .2px; }
</style>
</head>
<body>
<main class="canvas">
  <section class="card card--front" aria-label="Card front">
    <div class="brand">
      <span class="brand__dot"></span>
      <span class="brand__name">Plavex</span>
    </div>
  </section>

  <section class="card card--back" aria-label="Card back">
    <div class="brand">
      <span class="brand__dot"></span>
      <span class="brand__name">Plavex</span>
    </div>
    <div class="divider"></div>
    <div class="contact">
      <p class="contact__name">Harriet Dunmore</p>
      <p class="contact__role">CEO</p>
      <ul class="contact__list">
        <li class="contact__item">
          <svg class="contact__icon" viewBox="0 0 16 16"><circle cx="8" cy="8" r="7" fill="none" stroke="#7cc242" stroke-width="1.2"/><rect x="5.5" y="4" width="5" height="8" rx="1" fill="none" stroke="#9a9a9d" stroke-width="1"/></svg>
          01632 960418
        </li>
        <li class="contact__item">
          <svg class="contact__icon" viewBox="0 0 16 16"><circle cx="8" cy="8" r="7" fill="none" stroke="#7cc242" stroke-width="1.2"/><rect x="4.5" y="5.5" width="7" height="5" fill="none" stroke="#9a9a9d" stroke-width="1"/><path d="M4.5 5.5 8 8.3l3.5-2.8" fill="none" stroke="#9a9a9d" stroke-width="1"/></svg>
          Harriet@plavex.co.uk
        </li>
        <li class="contact__item">
          <svg class="contact__icon" viewBox="0 0 16 16"><circle cx="8" cy="8" r="7" fill="none" stroke="#7cc242" stroke-width="1.2"/><circle cx="8" cy="8" r="3.8" fill="none" stroke="#9a9a9d" stroke-width="1"/><path d="M4.2 8h7.6M8 4.2v7.6" stroke="#9a9a9d" stroke-width="1"/></svg>
          www.plavex.co.uk
        </li>
      </ul>
    </div>
    <p class="address">Brackwell House, Fenmoor Enterprise Park, Partridge Way, Norwich QB9 3KX</p>
  </section>
</main>
</body>
</html>
```